Business card design for my company.
I would like the card's background colour to be black. You can also see our web site to get an idea of our brand. https://www.tmwhomecrafting.com.au/
- Name
- Email

```html
<!DOCTYPE html>
<html lang="en">
<head>
<meta charset="UTF-8">
<title>TMW Home Crafting — Business Card</title>
<link href="https://fonts.googleapis.com/css2?family=Montserrat:wght@400;500;700;800&display=swap" rel="stylesheet">
<style>
  :root {
    --stage: #e6e6e4;
    --card: #1f1f1f;
    --card-back: #191919;
    --pattern: #232323;
    --green: #1f9a48;
    --white: #f4f4f4;
  }
  * { margin: 0; padding: 0; box-sizing: border-box; }
  html, body {
    width: 1200px; height: 900px; overflow: hidden;
    background: var(--stage);
    font-family: "Montserrat", sans-serif;
  }
  .stage {
    width: 1200px; height: 900px;
    display: flex; flex-direction: column;
    align-items: center; justify-content: center; gap: 40px;
  }
  .card {
    position: relative;
    width: 700px; height: 400px;
    border-radius: 22px;
    overflow: hidden;
    box-shadow: 0 10px 28px rgba(0,0,0,.22);
  }

  /* Back face */
  .card--back { background: var(--card-back); }
  .brand-pattern {
    position: absolute; inset: 0;
    background: linear-gradient(135deg, var(--pattern), #1a1a1a 55%, var(--pattern));
  }
  .back-brand {
    position: absolute; left: 462px; top: 226px;
    display: flex; align-items: center; gap: 8px;
    color: var(--white); font-weight: 700; font-size: 15px;
    letter-spacing: .08em; text-transform: uppercase;
    white-space: nowrap;
  }
  .brand-square { width: 12px; height: 12px; background: var(--green); flex: none; }

  /* Front face */
  .card--front { background: var(--card); }
  .accent-bar {
    position: absolute; left: 0; top: 70px;
    width: 28px; height: 62px; background: var(--green);
  }
  .person { position: absolute; left: 54px; top: 66px; }
  .person-name {
    color: var(--green); font-weight: 800; font-size: 32px;
    letter-spacing: .04em; text-transform: uppercase; line-height: 1;
    white-space: nowrap;
  }
  .person-role {
    color: var(--white); font-weight: 500; font-size: 20px;
    margin-top: 6px;
  }
  .front-brand {
    position: absolute; right: 44px; top: 120px;
    display: flex; align-items: center; gap: 16px;
    color: var(--white); font-weight: 800; font-size: 34px;
    line-height: 1.15;
    letter-spacing: .06em; text-transform: uppercase;
  }
  .front-brand .brand-square { width: 30px; height: 30px; }
  .brand-name { display: block; }
  .brand-name span { display: block; white-space: nowrap; }
  .contacts {
    position: absolute; left: 54px; bottom: 48px;
    list-style: none;
    display: flex; flex-direction: column; gap: 12px;
  }
  .contact {
    display: flex; align-items: center; gap: 12px;
    color: var(--white); font-size: 19px; font-weight: 500;
  }
  .contact svg { width: 18px; height: 18px; flex: none; }
</style>
</head>
<body>
<main class="stage">
  <section class="card card--back" aria-label="Card back">
    <div class="brand-pattern" role="img" aria-label="Repeating faint tonal brand pattern across the card back"></div>
    <div class="back-brand"><span class="brand-square"></span>TMW Home Crafting</div>
  </section>

  <section class="card card--front" aria-label="Card front">
    <div class="accent-bar"></div>
    <div class="person">
      <h1 class="person-name">Daniel Reeves</h1>
      <p class="person-role">CEO/Founder</p>
    </div>
    <div class="front-brand">
      <span class="brand-square"></span>
      <p class="brand-name"><span>TMW Home</span><span>Crafting</span></p>
    </div>
    <ul class="contacts">
      <li class="contact">
        <svg viewBox="0 0 24 24" aria-hidden="true"><path fill="#1f9a48" d="M6.6 10.8a15.1 15.1 0 0 0 6.6 6.6l2.2-2.2c.3-.3.7-.4 1-.2 1.1.4 2.3.6 3.6.6.6 0 1 .4 1 1V20c0 .6-.4 1-1 1A17 17 0 0 1 3 4c0-.6.4-1 1-1h3.5c.6 0 1 .4 1 1 0 1.3.2 2.5.6 3.6.1.3 0 .7-.2 1z"/></svg>
        897-555-0148
      </li>
      <li class="contact">
        <svg viewBox="0 0 24 24" aria-hidden="true"><rect x="2" y="5" width="20" height="14" rx="1.5" fill="#1f9a48"/><path d="M3 6l9 7 9-7" fill="none" stroke="#1f1f1f" stroke-width="1.8"/></svg>
        info@tmwhomecrafting.com.au
      </li>
      <li class="contact">
        <svg viewBox="0 0 24 24" aria-hidden="true" fill="none" stroke="#1f9a48" stroke-width="1.8"><circle cx="12" cy="12" r="9"/><ellipse cx="12" cy="12" rx="4" ry="9"/><path d="M3 12h18M5 7h14M5 17h14"/></svg>
        www.tmwhomecrafting.com.au
      </li>
    </ul>
  </section>
</main>
</body>
</html>
```